Animal Eye Clinic needs a Business card

We are a new veterinary ophthalmology practice (Ridgeline Pet Vision Care) and we need a business card designed. We only see animal eyes - we are not a regular veterinary clinic. We already have a logo. We are looking for a professional, good looking business card to hand out to our clients. We are looking for something simple but professional and contemporary. Our logo is likely the only picture/graphic that needs to be on the card.
Updates

Contact Information for Business Card

Delia Vossman, BSc, DVM, MSc, DipACVO
Veterinary Ophthalmologist

Phone: 250.418.3927
Email: ridgelinepetvisioncare@mailbox-example.net
Website: ridgelinepetvisioncare-example.net
Address: 1874 Thornbury Rd
Kelowna, BC, V1X 4M9

Colors

Designer to choose colors to be used in the design.

Requirements
Must have
• Our logo (attached)

```html
<!DOCTYPE html>
<html lang="en">
<head>
<meta charset="UTF-8">
<title>Ridgeline Pet Vision Care – Business Card</title>
<link rel="stylesheet" href="https://fonts.googleapis.com/css2?family=Roboto:wght@400;700&display=swap">
<style>
  :root {
    --backdrop: #232323;
    --card: #151515;
    --teal: #1b9bab;
    --grey: #9a9a9a;
    --grey-soft: #7d7d7d;
  }
  * { margin: 0; padding: 0; box-sizing: border-box; }
  html, body { width: 1200px; height: 900px; overflow: hidden; }
  body {
    background: var(--backdrop);
    font-family: "Roboto", Arial, sans-serif;
    position: relative;
  }
  .card {
    position: absolute;
    left: 250px;
    width: 700px;
    height: 400px;
    background: var(--card);
    box-shadow: 0 10px 30px rgba(0,0,0,0.45);
  }
  .card--front { top: 30px; }
  .card--back { top: 470px; }

  /* front face */
  .front-brand {
    position: absolute;
    inset: 0;
    display: flex;
    align-items: center;
    justify-content: center;
    gap: 18px;
  }
  .brand-dot {
    width: 44px; height: 44px;
    border-radius: 50%;
    background: var(--teal);
    flex: none;
  }
  .front-brand .brand-name {
    color: var(--teal);
    font-weight: 700;
    font-size: 32px;
    letter-spacing: 1px;
    text-transform: uppercase;
  }

  /* back face */
  .practice {
    position: absolute;
    left: 36px;
    top: 150px;
    width: 290px;
  }
  .practice-brand {
    display: flex;
    align-items: center;
    gap: 10px;
    margin-bottom: 12px;
  }
  .practice-brand .brand-dot { width: 30px; height: 30px; }
  .practice-brand .brand-name {
    color: var(--teal);
    font-weight: 700;
    font-size: 17px;
    text-transform: uppercase;
    letter-spacing: 0.5px;
  }
  .practice-address {
    color: var(--grey-soft);
    font-size: 14px;
    white-space: nowrap;
  }
  .divider {
    position: absolute;
    left: 340px;
    top: 110px;
    width: 2px;
    height: 190px;
    background: var(--teal);
  }
  .person {
    position: absolute;
    left: 360px;
    top: 112px;
    width: 330px;
  }
  .person-name {
    color: var(--teal);
    font-weight: 700;
    font-size: 34px;
    line-height: 1;
    text-transform: uppercase;
    letter-spacing: 1px;
  }
  .person-credentials {
    color: var(--teal);
    font-weight: 700;
    font-size: 15px;
    margin-top: 4px;
  }
  .person-title {
    color: var(--grey);
    font-size: 15px;
    margin-top: 2px;
    margin-bottom: 10px;
  }
  .contact-list { list-style: none; }
  .contact-item {
    display: flex;
    align-items: center;
    gap: 8px;
    color: var(--grey);
    font-size: 13.5px;
    margin-top: 6px;
    white-space: nowrap;
  }
  .contact-icon { width: 16px; height: 16px; flex: none; }
</style>
</head>
<body>

<section class="card card--front" aria-label="Business card front">
  <div class="front-brand">
    <span class="brand-dot"></span>
    <span class="brand-name">Ridgeline Pet Vision Care</span>
  </div>
</section>

<section class="card card--back" aria-label="Business card back">
  <div class="practice">
    <div class="practice-brand">
      <span class="brand-dot"></span>
      <span class="brand-name">Ridgeline Pet Vision Care</span>
    </div>
    <p class="practice-address">1874 Thornbury Rd, Kelowna, BC, V1X 4M9</p>
  </div>

  <div class="divider"></div>

  <div class="person">
    <h1 class="person-name">Delia Vossman</h1>
    <p class="person-credentials">BSc, DVM, MSc, DipACVO</p>
    <p class="person-title">Veterinary Ophthalmologist</p>
    <ul class="contact-list">
      <li class="contact-item">
        <svg class="contact-icon" viewBox="0 0 16 16" fill="none" stroke="var(--teal)" stroke-width="1.3">
          <circle cx="8" cy="8" r="7"/>
          <path d="M5.5 4.5l1.5 0 .6 1.8-1 .8a5 5 0 0 0 2.3 2.3l.8-1 1.8.6 0 1.5c-3.5.3-6.3-2.5-6-6z"/>
        </svg>
        250.418.3927
      </li>
      <li class="contact-item">
        <svg class="contact-icon" viewBox="0 0 16 16" fill="none" stroke="var(--teal)" stroke-width="1.3">
          <rect x="1" y="3.5" width="14" height="9"/>
          <path d="M1 3.5l7 5 7-5"/>
        </svg>
        ridgelinepetvisioncare@mailbox-example.net
      </li>
      <li class="contact-item">
        <svg class="contact-icon" viewBox="0 0 16 16" fill="none" stroke="var(--teal)" stroke-width="1.3">
          <circle cx="8" cy="8" r="7"/>
          <ellipse cx="8" cy="8" rx="3" ry="7"/>
          <path d="M1 8h14M2.2 4.5h11.6M2.2 11.5h11.6"/>
        </svg>
        www.ridgelinepetvisioncare-example.net
      </li>
    </ul>
  </div>
</section>

</body>
</html>
```